VOR Exterior Coatings

double sided. the front i want the name of the business each word on a new line with the VOR being bigger. id like teal, black and white colors. the back i want my contact info. Flat, no gloss. Something professional and I want to feel the letters bump put of the card. if possible maybe a paint sprayer in corner. not a car paint spray. (no tank on top of gun)
no vehicle paint sprayers. that means no tank on top of the gun. doesn't have to have a sprayer. black/dark background on the front. white back ground on back with info

```html
<!DOCTYPE html>
<html lang="en">
<head>
<meta charset="utf-8">
<title>VOR Exterior Coatings – Business Card</title>
<link rel="stylesheet" href="https://fonts.googleapis.com/css2?family=Montserrat:wght@500;800&family=Arimo:wght@400&display=swap">
<style>
  :root {
    --stage: #141414;
    --stage-light: #242424;
    --teal: #00847f;
    --ink: #111111;
    --paper: #ffffff;
    --rule: #e3e3e3;
    --muted: #3a3a3a;
    --stamp: #5a5a5a;
    --card-dark: #030303;
  }
  * { margin: 0; padding: 0; box-sizing: border-box; }
  html, body { width: 1200px; height: 820px; overflow: hidden; }
  body {
    background: radial-gradient(ellipse at 50% 45%, var(--stage-light) 0%, var(--stage) 70%);
    font-family: "Arimo", Arial, sans-serif;
  }
  .canvas { position: relative; width: 1200px; height: 820px; }

  .card {
    position: absolute;
    top: 250px;
    width: 525px;
    height: 300px;
    border-radius: 3px;
    box-shadow: 0 14px 40px rgba(0,0,0,.6);
  }

  /* Back: contact side */
  .card--contact {
    left: 55px;
    background: var(--paper);
    border-bottom: 3px solid var(--teal);
  }
  .brand-name {
    position: absolute;
    right: 40px;
    top: 38px;
    font-family: "Montserrat", Arial, sans-serif;
    font-weight: 800;
    color: var(--ink);
    text-transform: uppercase;
    line-height: 1.02;
    text-align: left;
    font-size: 26px;
    letter-spacing: 1px;
  }
  .brand-name .brand-line--lead { font-size: 44px; letter-spacing: 4px; }
  .divider {
    position: absolute;
    left: 210px; right: 30px; top: 168px;
    height: 1px;
    background: var(--rule);
  }
  .person {
    position: absolute;
    left: 34px; top: 178px;
  }
  .person-name {
    font-family: "Montserrat", Arial, sans-serif;
    font-weight: 500;
    font-size: 18px;
    color: var(--teal);
    text-transform: uppercase;
    letter-spacing: -.2px;
  }
  .person-role { font-size: 13px; color: var(--muted); margin-top: 1px; }
  .contact-list {
    position: absolute;
    left: 36px; top: 230px;
    list-style: none;
  }
  .contact-list li {
    display: flex; align-items: center; gap: 7px;
    font-size: 13px; color: var(--muted); line-height: 19px;
  }
  .contact-list svg { width: 13px; height: 13px; flex: none; }
  .address {
    position: absolute;
    right: 36px; top: 200px;
    font-size: 13px; color: var(--muted); line-height: 18px;
    text-align: left;
  }

  /* Front: brand side */
  .card--brand {
    left: 620px;
    background: var(--card-dark);
    border-bottom: 6px solid var(--teal);
    display: flex; align-items: center; justify-content: center;
  }
  .card--brand .brand-name {
    position: static;
    color: var(--stamp);
    font-size: 30px;
  }
  .card--brand .brand-name .brand-line--lead { font-size: 54px; }
</style>
</head>
<body>
<main class="canvas">

  <section class="card card--contact" aria-label="Business card, contact side">
    <div class="brand-name">
      <div class="brand-line--lead">VOR</div>
      <div>Exterior</div>
      <div>Coatings</div>
    </div>
    <div class="divider"></div>

    <div class="person">
      <p class="person-name">Marcus Bell</p>
      <p class="person-role">Managing Director</p>
    </div>

    <ul class="contact-list">
      <li>
        <svg viewBox="0 0 14 14" aria-hidden="true"><rect x=".7" y=".7" width="12.6" height="12.6" rx="2" fill="none" stroke="#00847f" stroke-width="1.2"/><path d="M4 3.5l1.6-.4.9 2-1 .8a5 5 0 0 0 2.6 2.6l.8-1 2 .9-.4 1.6C7 10.2 3.8 7 4 3.5z" fill="#00847f"/></svg>
        044-555 210 347
      </li>
      <li>
        <svg viewBox="0 0 14 14" aria-hidden="true"><rect x=".5" y="2.5" width="13" height="9" fill="#00847f"/><path d="M.5 2.5l6.5 5 6.5-5" fill="none" stroke="#fff" stroke-width="1"/></svg>
        info@vorcoat.com
      </li>
      <li>
        <svg viewBox="0 0 14 14" aria-hidden="true"><circle cx="7" cy="7" r="6.3" fill="#00847f"/><g fill="none" stroke="#fff" stroke-width=".8"><ellipse cx="7" cy="7" rx="2.6" ry="6.3"/><path d="M.7 7h12.6M1.8 4h10.4M1.8 10h10.4"/></g></svg>
        www.vorcoat.com
      </li>
    </ul>

    <p class="address">88, Harbor Road<br>Eastland, 30218</p>
  </section>

  <section class="card card--brand" aria-label="Business card, brand side">
    <div class="brand-name">
      <div class="brand-line--lead">VOR</div>
      <div>Exterior</div>
      <div>Coatings</div>
    </div>
  </section>

</main>
</body>
</html>
```